Business Card for Olive Drift-Eco Friendly Organic Clothing Brand

We are looking for an amazing business card for our eco friendly, organic clothing brand. We are thinking maybe a business card with a peel off sticker on the back, since our hanging clothing tag is a peel off sticker on the back. I will attach our hang tag so we can make sure we stay in line with our design. I've also attached a bag we are doing because I do like the scattered emblem look as well.

```html
<!DOCTYPE html>
<html lang="en">
<head>
<meta charset="utf-8">
<title>Olive Drift – Business Card</title>
<link href="https://fonts.googleapis.com/css2?family=Open+Sans:wght@400;600;700&display=swap" rel="stylesheet">
<style>
  :root {
    --backdrop: #161616;
    --card-white: #ffffff;
    --olive-dark: #1c2014;
    --ink: #1a1a1a;
    --muted: #9a9a9a;
    --gold: #e2b93b;
    --gold-light: #f6de84;
    --pattern-dark: #2b2b26;
  }
  * { margin: 0; padding: 0; box-sizing: border-box; }
  html, body {
    width: 1200px; height: 900px; overflow: hidden;
    background: var(--backdrop);
    font-family: "Open Sans", Arial, sans-serif;
  }
  .canvas { position: relative; width: 1200px; height: 900px; }

  .card { position: absolute; top: 170px; width: 347px; height: 561px; overflow: hidden; }

  /* Front */
  .card-front { left: 259px; background: var(--card-white); }
  .tab { position: absolute; left: 102px; width: 143px; background: var(--olive-dark); }
  .tab-top { top: 0; height: 30px; }
  .tab-bottom { bottom: 0; height: 28px; }

  .brand {
    position: absolute; top: 160px; left: 0; width: 100%;
    display: flex; align-items: center; justify-content: center; gap: 12px;
  }
  .brand-mark { width: 22px; height: 22px; background: var(--olive-dark); }
  .brand-name { font-size: 30px; font-weight: 700; color: var(--olive-dark); }
  .brand-url {
    position: absolute; top: 210px; width: 100%; text-align: center;
    font-size: 11px; color: var(--muted);
  }

  .person { position: absolute; top: 286px; width: 100%; text-align: center; }
  .person-name { font-size: 18px; font-weight: 600; color: var(--ink); line-height: 22px; }
  .person-title { font-size: 14.5px; color: var(--muted); line-height: 20px; }

  .address {
    position: absolute; top: 341px; width: 100%; text-align: center;
    font-size: 14.5px; color: var(--muted); line-height: 20px;
  }

  .contacts {
    position: absolute; top: 396px; width: 100%;
    list-style: none; text-align: center;
    font-size: 14.5px; color: var(--muted); line-height: 20px;
  }
  .contacts li { display: flex; justify-content: center; align-items: center; gap: 6px; }
  .contacts svg { width: 10px; height: 10px; fill: var(--ink); }

  /* Back */
  .card-back { left: 631px; background: var(--pattern-dark); }
  .word-pattern {
    position: absolute; inset: 0 0 78px 0;
    background: linear-gradient(135deg, #3a3526 0%, #2a2a24 40%, #4a3d1e 70%, #2a2a24 100%);
  }
  .back-band {
    position: absolute; left: 0; right: 0; bottom: 0; height: 78px;
    background: var(--pattern-dark);
    display: flex; align-items: center; justify-content: center;
  }
  .back-name { font-size: 34px; font-weight: 700; color: var(--gold); }
</style>
</head>
<body>
<main class="canvas">

  <section class="card card-front">
    <div class="tab tab-top"></div>

    <div class="brand">
      <span class="brand-mark"></span>
      <span class="brand-name">Olive Drift</span>
    </div>
    <p class="brand-url">www.olivedrift.com</p>

    <div class="person">
      <p class="person-name">Elliot Marsh</p>
      <p class="person-title">Managing Director</p>
    </div>

    <p class="address">12345, Address Goes Here<br>Country Name, 123456.</p>

    <ul class="contacts">
      <li>
        <svg viewBox="0 0 10 10" aria-hidden="true"><path d="M2 0.5 L3.6 2.6 L2.7 3.7 Q3.8 5.9 6.3 7.3 L7.4 6.4 L9.5 8 L8.3 9.5 Q3.5 9 0.5 1.7 Z"/></svg>
        044-123 456 789
      </li>
      <li>
        <svg viewBox="0 0 10 10" aria-hidden="true"><path d="M0.5 2 H9.5 V8.5 H0.5 Z M0.5 2 L5 5.5 L9.5 2" stroke="#fff" stroke-width="0.8"/></svg>
        info@webname.com
      </li>
      <li>
        <svg viewBox="0 0 10 10" aria-hidden="true"><circle cx="5" cy="5" r="4.6"/></svg>
        www.websitename.com
      </li>
    </ul>

    <div class="tab tab-bottom"></div>
  </section>

  <section class="card card-back">
    <div class="word-pattern" role="img" aria-label="Repeating gold-foil word pattern: love, peace, namaste, inspire, live, om, hearts and peace signs on dark olive"></div>
    <div class="back-band">
      <span class="back-name">Olive Drift</span>
    </div>
  </section>

</main>
</body>
</html>
```